Brightmoor Talent company

We require a website for job recruitment company called "Brightmoor Talent"
Our company is specialising in recruitment of skilled labour from Sri Lanka into Australian market.
We would like to include a job advertising plugin where jobs can be listed and applied for .
COPYWRITING MUST BE INCLUDED !

Industry/Entity Type

Recruitment

Coding

Coded - Design and coding required

Number of Pages Required

5+ page

Colors

Designer to choose colors to be used in the design.

```html
<!DOCTYPE html>
<html lang="en">
<head>
<meta charset="utf-8">
<title>Brightmoor Talent – Recruitment Agency</title>
<link href="https://fonts.googleapis.com/css2?family=Arimo:ital,wght@0,400;0,700;1,400&display=swap" rel="stylesheet">
<style>
:root{
  --ink:#1c1d21;
  --white:#ffffff;
  --slate:#868c99;
  --slate-dark:#6f7583;
  --brand:#1f3f8a;
  --accent:#4a88c9;
  --nav:#3a3d44;
  --dark:#25272d;
  --footer:#333436;
  --field:#ffffff;
}
*{box-sizing:border-box;margin:0;padding:0}
html,body{width:1200px;height:3298px;overflow:hidden}
body{position:relative;font-family:"Arimo",Arial,sans-serif;color:var(--ink);background:var(--slate)}
.abs{position:absolute}
.photo{position:absolute}

/* header */
.site-header{left:0;top:0;width:1200px;height:63px;background:var(--white)}
.brand{left:83px;top:14px;font-size:26px;font-weight:700;color:var(--brand);letter-spacing:.3px}
.nav{right:182px;top:22px;display:flex;gap:36px;font-size:15px;font-weight:700;color:var(--nav)}
.nav .active{color:var(--accent)}

/* hero */
.hero{left:0;top:63px;width:1200px;height:727px;background:linear-gradient(115deg,#2c2f36 0%,#555a63 35%,#b9a48f 55%,#d9d5cf 75%,#8d8f93 100%)}
.hero-shade{left:0;top:63px;width:1200px;height:727px;background:linear-gradient(180deg,rgba(0,0,0,0) 45%,rgba(0,0,0,.45) 100%)}
.register{left:987px;top:85px;width:104px;height:39px;border-radius:20px;background:#8a8f99;color:var(--white);font-size:15px;display:flex;align-items:center;justify-content:center}
.hero-title{left:0;width:1200px;top:525px;text-align:center;color:var(--white);font-size:56px;font-weight:700}
.hero-sub{left:0;width:1200px;top:586px;text-align:center;color:var(--white);font-size:34px}
.hero-copy{left:83px;width:1034px;top:642px;text-align:center;color:var(--white);font-size:14px;line-height:22.5px}

/* model */
.band-model{left:0;top:790px;width:1200px;height:567px;background:var(--slate)}
.h-shadow{text-shadow:2px 3px 4px rgba(0,0,0,.45)}
.model-title{left:680px;top:893px;font-size:44px;font-weight:700;color:var(--white)}
.model-copy{left:618px;top:960px;width:454px;font-size:15.5px;line-height:25.5px;color:var(--white);text-align:justify}
.model-copy p+p{margin-top:25px}
.btn-outline{left:619px;top:1236px;width:146px;height:44px;border:2px solid var(--ink);color:var(--ink);font-size:15px;font-weight:700;display:flex;align-items:center;justify-content:center}

/* profile */
.band-profile{left:0;top:1357px;width:1200px;height:336px;background:var(--white)}
.profile-title{left:647px;top:1390px;font-size:33px;line-height:36px;font-weight:700;color:var(--ink)}
.profile-copy{left:647px;top:1480px;width:390px;font-size:14px;line-height:22.5px}
.btn-blue{height:38px;width:111px;background:var(--accent);color:var(--white);font-size:14px;display:flex;align-items:center;justify-content:center;letter-spacing:.5px}

/* cv */
.cv-panel{left:83px;top:1693px;width:517px;height:375px;background:linear-gradient(180deg,#a8c3e0 0%,#8d9bb0 60%,var(--slate) 100%)}
.cv-title{left:138px;top:1775px;font-size:33px;line-height:35px;font-weight:700;color:var(--ink)}
.cv-copy{left:120px;top:1891px;width:375px;font-size:14px;line-height:22.5px}

/* advice */
.advice-title{left:0;width:1200px;top:2093px;text-align:center;font-size:44px;font-weight:700;color:var(--white)}
.avatar{width:220px;height:220px;border-radius:50%}
.advice-copy{width:210px;font-size:14px;line-height:25.5px;font-style:italic;color:var(--white)}

/* notify */
.notify-title{left:110px;width:415px;top:2765px;text-align:center;font-size:32px;line-height:35px;font-weight:700;color:var(--white)}
.label{font-size:14px;color:var(--white)}
.field{height:40px;background:var(--field);border-radius:3px;font-size:14px;color:#8b8f96;padding:0 11px;display:flex;align-items:center}
.submit{left:110px;top:3014px;width:415px;height:49px;border-radius:3px;background:var(--dark);color:var(--white);font-weight:700;font-size:14px;display:flex;align-items:center;justify-content:center}
.alert-icon{left:628px;top:2740px;width:76px;height:76px;border-radius:50%;background:var(--white)}

/* footer */
.site-footer{left:0;top:3135px;width:1200px;height:75px;background:var(--white)}
.footer-brand{left:83px;top:3157px;font-size:28px;font-weight:700;color:var(--brand)}
.social{width:50px;height:50px;border-radius:50%;background:var(--slate-dark);top:3148px}
.bottom-bar{left:0;top:3210px;width:1200px;height:88px;background:var(--footer)}
.credit{left:0;width:1200px;top:3246px;text-align:center;font-size:11px;color:var(--white)}
.credit u{color:#a9c8ee}
</style>
</head>
<body>
<header class="abs site-header">
  <div class="abs brand">Brightmoor Talent</div>
  <nav class="abs nav"><span>Home</span><span class="active">Work</span><span>About us</span><span>Contact us</span></nav>
</header>

<section>
  <div class="photo hero" role="img" aria-label="Two professionals in suits shaking hands"></div>
  <div class="abs hero-shade"></div>
  <div class="abs register">Register</div>
  <h1 class="abs hero-title h-shadow">Recruitment</h1>
  <div class="abs hero-sub">Agency</div>
  <p class="abs hero-copy">Recruitment Agency that strives to help businesses put together a staff of highly efficient and skilled professionals, and also serve employees by opening up new vistas of job opportunities for them. We take pride in lending our hand in creating the kind of professional environment that would fulfill the mission and vision that enterprises are built upon.</p>
</section>

<section>
  <div class="abs band-model"></div>
  <div class="photo" style="left:83px;top:845px;width:508px;height:488px;background:linear-gradient(135deg,#e9e8e4,#c9c7c1 50%,#4a4a40)" role="img" aria-label="Recruiter seated at an office desk"></div>
  <h2 class="abs model-title h-shadow">Recruitment Model</h2>
  <div class="abs model-copy">
    <p>Engage With Service Models For Enhancing Business Processes. We boasts a set of different recruitment processes that provide perfect answer to your needs. Supported by effectively planned payroll processes, it helps you maximize your business functions and output through quality resources.</p>
    <p>We understand that every company has a different hiring process and specific sets of skills. That's why we offer solutions tailored to your needs. We set premium on timely delivery and quality.</p>
  </div>
  <div class="abs btn-outline">READ MORE</div>
</section>

<section>
  <div class="abs band-profile"></div>
  <div class="photo" style="left:83px;top:1357px;width:510px;height:326px;background:linear-gradient(120deg,#3d3e44,#6b6c72 55%,#e4ddd2)" role="img" aria-label="Hand holding a smartphone"></div>
  <h2 class="abs profile-title h-shadow">Create and build your<br>profile</h2>
  <p class="abs profile-copy">List your trade, licences and experience once, then apply for open Australian job listings in a few clicks.</p>
  <div class="abs btn-blue" style="left:787px;top:1560px">CREATE</div>
</section>

<section>
  <div class="abs cv-panel"></div>
  <h2 class="abs cv-title">Drop your CV<br>Get Hired!!</h2>
  <p class="abs cv-copy">Upload your CV and our team will match you with verified roles from Australian employers.</p>
  <div class="abs btn-blue" style="left:150px;top:1973px">CREATE</div>
  <div class="photo" style="left:600px;top:1693px;width:516px;height:375px;background:linear-gradient(135deg,#a9572d 0%,#8a4422 55%,#7d3a1c 100%)" role="img" aria-label="Curriculum vitae page with a pen on a wooden desk"></div>
</section>

<section>
  <h2 class="abs advice-title h-shadow">Advice from our expertise</h2>
  <div class="photo avatar" style="left:102px;top:2190px;background:linear-gradient(160deg,#f2f0ee,#6d2a3e)" role="img" aria-label="Advisor portrait"></div>
  <p class="abs advice-copy" style="left:369px;top:2248px">Keep your skills assessment and trade certificates current before you apply for sponsored roles.</p>
  <div class="photo avatar" style="left:619px;top:2190px;background:linear-gradient(160deg,#eeeeee,#3b4f74)" role="img" aria-label="Advisor portrait"></div>
  <p class="abs advice-copy" style="left:886px;top:2248px">Tailor each application to the job listing and name the tools and machinery you know.</p>
  <div class="photo avatar" style="left:102px;top:2453px;background:linear-gradient(160deg,#f4f3f1,#2a2726)" role="img" aria-label="Advisor portrait"></div>
  <p class="abs advice-copy" style="left:369px;top:2511px">Practise your English test early; strong results open more visa pathways in Australia.</p>
  <div class="photo avatar" style="left:619px;top:2453px;background:linear-gradient(160deg,#c9cdd2,#2b2b2e)" role="img" aria-label="Advisor portrait"></div>
  <p class="abs advice-copy" style="left:886px;top:2511px">Employers value references, so ask past supervisors to confirm your work history.</p>
</section>

<section>
  <h2 class="abs notify-title h-shadow">Get Notified Your Every<br>New Job</h2>
  <div class="abs label" style="left:110px;top:2857px">EMAIL</div>
  <div class="abs label" style="left:326px;top:2857px">NAME</div>
  <div class="abs field" style="left:110px;top:2877px;width:200px">Enter a valid email address</div>
  <div class="abs field" style="left:326px;top:2877px;width:199px">Enter your Name</div>
  <div class="abs label" style="left:110px;top:2937px">ADDRESS</div>
  <div class="abs field" style="left:110px;top:2957px;width:415px">Enter your address</div>
  <div class="abs submit">SUBMIT</div>
  <div class="photo" style="left:618px;top:2730px;width:480px;height:357px;background:linear-gradient(135deg,#f1efeb,#d8d6d1 45%,#2a2b2e 75%)" role="img" aria-label="Folded newspaper beside a laptop keyboard"></div>
  <div class="abs alert-icon">
    <svg width="76" height="76" viewBox="0 0 76 76" fill="none" stroke="#1c1d21" stroke-width="2.5">
      <rect x="28" y="18" width="20" height="38" rx="3"/>
      <line x1="33" y1="23" x2="43" y2="23"/>
      <circle cx="38" cy="50" r="2"/>
      <path d="M22 28 q-4 10 0 20 M17 25 q-6 13 0 26 M54 28 q4 10 0 20 M59 25 q6 13 0 26"/>
    </svg>
  </div>
</section>

<footer>
  <div class="abs site-footer"></div>
  <div class="abs footer-brand">Brightmoor Talent</div>
  <div class="abs social" style="left:932px" aria-label="Social link"></div>
  <div class="abs social" style="left:993px" aria-label="Social link"></div>
  <div class="abs social" style="left:1053px" aria-label="Social link"></div>
  <div class="abs bottom-bar"></div>
  <p class="abs credit"><u>Website Templates</u> created with <u>Website Builder Software</u>.</p>
</footer>
</body>
</html>
```